Business card design needed

Family General Practitioner/ Family Physician.
Logo is the logo of the Noble Guild of Family Healers Oceania
http://kpltw.varendo.example/ImageShelf/marks/pages/NGFHO%20mark_jpg.htm
Updates

Project Deadline Extended
Reason: Just a bit more time to make changes and the weekend for me to look at things closely and to choose. Thanks, Orin

Thanks for all the submissions. So many of them are really works of art. Not one of them are not good. The ones that I am eliminating are the ones that I think are not suitable for me personally only, and because if I don't, it makes it very difficult to decide as many of you are also sending me slight variations of a card. I have just decided to choose a second place card too. Can't thank you all enough. Good luck, Orin. P.S - Working today till 10 pm as the card says :-), so probably won't be able to give a feedback till late Saturday night or Sunday morning here in Sydney, Australia. 

Project Deadline Extended
Reason: Just added a second place to the budget and realised that Australia is ahead of the rest of the world in the time zone (only :-) - don't want to offend anyone or start a debate!! ) , so Monday deadline will mean it will be a weekend for the rest of the world. Just wanted to give everyone more time to submit their best, especially since I will be picking a second card too. Can't thank everyone enough for the submissions. P.S - Not keen on photos on the card.

Industry/Entity Type

Business

Contact Information for Business Card

Dr. Orin Halvey M.B.B.S., F.N.G.F.H.O
Family General Practitioner
Address, timings, phone and fax number on the back.

Requirements
Must have
• Timings
Mon 7 am - 7 pm
Tues 7 am - 12 pm
Wed 7 am - 10 pm
Thurs 7 am - 12 pm
Fri 7 am - 8 pm
Sat 8 am - 10 pm
Sun - Off

```html
<!DOCTYPE html>
<html lang="en">
<head>
<meta charset="utf-8">
<title>Dr. Orin Halvey – Business Card</title>
<link rel="stylesheet" href="https://fonts.googleapis.com/css2?family=Open+Sans:wght@400;600;700&display=swap">
<style>
  :root {
    --backdrop: #e8d2a6;
    --card: #ffffff;
    --accent-green: #6a9a4a;
    --accent-red: #b3231c;
    --brand-blue: #1f7fb6;
    --ink: #1e1e1e;
    --band-grey: #dedede;
  }
  html, body {
    margin: 0;
    padding: 0;
    width: 1200px;
    height: 378px;
    overflow: hidden;
    background: var(--backdrop);
    font-family: "Open Sans", sans-serif;
    color: var(--ink);
  }
  .stage {
    position: relative;
    width: 1200px;
    height: 378px;
  }
  .card {
    position: absolute;
    background: var(--card);
    box-sizing: border-box;
    overflow: hidden;
  }
  /* Front */
  .card-front {
    left: 46px;
    top: 32px;
    width: 540px;
    height: 309px;
    border-top: 4px solid var(--accent-green);
    border-bottom: 4px solid var(--accent-red);
  }
  .guild-mark {
    position: absolute;
    left: 34px;
    top: 86px;
    width: 160px;
    text-align: center;
  }
  .guild-mark .guild-dot {
    display: block;
    width: 34px;
    height: 34px;
    margin: 0 auto 10px;
    border-radius: 50%;
    background: var(--brand-blue);
  }
  .guild-mark .guild-name {
    font-size: 15px;
    font-weight: 600;
    line-height: 1.3;
    color: var(--brand-blue);
  }
  .identity {
    position: absolute;
    left: 236px;
    top: 98px;
    color: var(--brand-blue);
  }
  .identity .doctor-name {
    margin: 0;
    font-size: 34px;
    font-weight: 400;
    line-height: 1.1;
    letter-spacing: -0.3px;
  }
  .identity .credentials {
    margin: 12px 0 0;
    font-size: 12px;
  }
  .identity .role {
    margin: 14px 0 0;
    font-size: 17px;
  }
  /* Back */
  .card-back {
    left: 612px;
    top: 34px;
    width: 540px;
    height: 307px;
    border-bottom: 4px solid var(--accent-red);
  }
  .hours-title {
    position: absolute;
    top: 26px;
    left: 0;
    width: 100%;
    margin: 0;
    text-align: center;
    font-size: 26px;
    font-weight: 400;
  }
  .hours {
    position: absolute;
    left: 173px;
    top: 80px;
    border-collapse: collapse;
    font-size: 14px;
  }
  .hours td {
    padding: 0;
    height: 19.2px;
    line-height: 19.2px;
  }
  .hours .day { width: 92px; }
  .hours .sep { width: 23px; }
  .contact-band {
    position: absolute;
    left: 0;
    bottom: 0;
    width: 100%;
    height: 66px;
    background: var(--band-grey);
    text-align: center;
    font-size: 11.5px;
    font-weight: 700;
    line-height: 19px;
    padding-top: 14px;
    box-sizing: border-box;
  }
  .contact-band p { margin: 0; }
</style>
</head>
<body>
<main class="stage">
  <section class="card card-front">
    <div class="guild-mark">
      <span class="guild-dot"></span>
      <span class="guild-name">Noble Guild of Family Healers Oceania</span>
    </div>
    <div class="identity">
      <h1 class="doctor-name">Dr. Orin Halvey</h1>
      <p class="credentials">M.B.B.S., F.N.G.F.H.O</p>
      <p class="role">Family General Practitioner</p>
    </div>
  </section>

  <section class="card card-back">
    <h2 class="hours-title">Timing</h2>
    <table class="hours">
      <tr><td class="day">Monday</td><td class="sep">:</td><td>7 AM - &nbsp;&nbsp;7 PM</td></tr>
      <tr><td class="day">Tuesday</td><td class="sep">:</td><td>7 AM - 12 PM</td></tr>
      <tr><td class="day">Wednesday</td><td class="sep">:</td><td>7 AM - 10 PM</td></tr>
      <tr><td class="day">Thursday</td><td class="sep">:</td><td>7 AM - 12 PM</td></tr>
      <tr><td class="day">Friday</td><td class="sep">:</td><td>7 AM - &nbsp;&nbsp;8 PM</td></tr>
      <tr><td class="day">Saturday</td><td class="sep">:</td><td>8 AM - 10 PM</td></tr>
      <tr><td class="day">Sunday</td><td class="sep">:</td><td>OFF</td></tr>
    </table>
    <div class="contact-band">
      <p>Upper Level, Marlowe Court, Brindlecourt Plaza, Fernvale, NSW 2999</p>
      <p>P: 02 5550 1846 F: 02 5550 1872</p>
    </div>
  </section>
</main>
</body>
</html>
```